Machining Business Order Thank You Insert

I am looking for a business style card to include with orders that I ship. The card needs to thank the recipient for their order, and encourage them to leave a review. The card should include my business name and contact information and have an area to hand write a message.

I mainly sale on Craftlane and my own website. We are a machining an manufacturing business that are in the sale of mostly metal machined and 3d printed plastic products.

The front of the card should include the following:
Logo: (attached)
Snapgram: https://www.snapgram.example/kelvomill/
Friendsbook: https://www.friendsbook.example/KelvoMill
Website: https://www.kelvomill.example/

The back of the card needs an area to write a message

Industry/Entity Type

3D Printing, Machining, Craftlane

Contact Information for Business Card

Black or white front, white back to write a personal message

Font styles to use
Sans Serif

Colors

Designer to choose colors to be used in the design.

Requirements
Must have
• Encourage a review, social media info

```html
<!DOCTYPE html>
<html lang="en">
<head>
<meta charset="utf-8">
<title>KelvoMill – Thank You Insert</title>
<link rel="stylesheet" href="https://fonts.googleapis.com/css2?family=Barlow:wght@400;500;600&family=Barlow+Semi+Condensed:wght@500&family=Kaushan+Script&display=swap">
<style>
  :root {
    --stage: #8b8e90;
    --card-white: #ffffff;
    --card-dark-top: #3a3a3a;
    --card-dark-bottom: #0c0c0c;
    --orange: #e55a24;
    --grey: #6b6b6b;
    --ink: #333333;
    --line-text: #9a9a9a;
  }
  * { margin: 0; padding: 0; box-sizing: border-box; }
  html, body { width: 1200px; height: 928px; overflow: hidden; }
  body { background: var(--stage); position: relative; font-family: "Barlow", sans-serif; }

  .card { position: absolute; border-radius: 16px; overflow: hidden; }

  /* Note side */
  .card--note { left: 267px; top: 59px; width: 670px; height: 383px; background: var(--card-white); }
  .brand { position: absolute; left: 50px; top: 100px; width: 206px; text-align: center; }
  .brand__mark { display: block; width: 92px; height: 92px; margin: 0 auto 64px; background: var(--orange); }
  .brand__name {
    font-family: "Barlow Semi Condensed", sans-serif; font-weight: 500;
    font-size: 27px; line-height: 1; letter-spacing: 9px; color: var(--grey); padding-left: 9px;
  }
  .write-lines { position: absolute; left: 295px; top: 99px; width: 312px; }
  .write-lines__rule { display: block; width: 312px; height: 2px; margin-bottom: 89px; }

  /* Thank-you side */
  .card--thanks { left: 264px; top: 484px; width: 676px; height: 387px;
    background: linear-gradient(180deg, var(--card-dark-top) 0%, #222 55%, var(--card-dark-bottom) 100%); }
  .headline { position: absolute; inset: 0; }
  .headline__thank { position: absolute; left: 231px; top: 108px; font-family: "Kaushan Script", cursive;
    font-size: 64px; line-height: 1; color: var(--orange); transform: rotate(-3deg); }
  .headline__you { position: absolute; left: 233px; top: 176px; font-family: "Kaushan Script", cursive;
    font-size: 68px; line-height: 1; color: var(--grey); transform: rotate(-4deg); }
  .headline__for { position: absolute; left: 372px; top: 202px; font-weight: 500; font-size: 28px;
    line-height: 1; color: var(--orange); transform: rotate(-10deg); }
  .headline__order { position: absolute; left: 252px; top: 276px; font-weight: 500; font-size: 29px;
    line-height: 1; transform: rotate(-12deg); transform-origin: left bottom; white-space: nowrap; }
  .headline__order .your { color: var(--orange); }
  .headline__order .order { color: var(--grey); letter-spacing: 1px; }

  .review { position: absolute; left: 22px; top: 335px; display: flex; align-items: center;
    font-size: 18px; line-height: 1; color: var(--line-text); white-space: nowrap; letter-spacing: 0.6px; }
  .review__label { font-weight: 600; margin-right: 13px; }
  .review__item { display: flex; align-items: center; margin-right: 16px; }
  .review__item:last-child { margin-right: 0; }
  .review__dot { width: 18px; height: 18px; background: var(--orange); margin-right: 7px; border-radius: 3px; }
  .review__dot--round { border-radius: 50%; }
</style>
</head>
<body>

<section class="card card--note" aria-label="Card side for a handwritten message">
  <div class="brand">
    <span class="brand__mark"></span>
    <div class="brand__name">KELVOMILL</div>
  </div>
  <div class="write-lines">
    <svg class="write-lines__rule" viewBox="0 0 312 2"><line x1="0" y1="1" x2="312" y2="1" stroke="#333" stroke-width="1.5" stroke-dasharray="9 7"/></svg>
    <svg class="write-lines__rule" viewBox="0 0 312 2"><line x1="0" y1="1" x2="312" y2="1" stroke="#333" stroke-width="1.5" stroke-dasharray="9 7"/></svg>
    <svg class="write-lines__rule" viewBox="0 0 312 2"><line x1="0" y1="1" x2="312" y2="1" stroke="#333" stroke-width="1.5" stroke-dasharray="9 7"/></svg>
  </div>
</section>

<section class="card card--thanks" role="img" aria-label="Brushed dark metal card surface">
  <div class="headline">
    <div class="headline__thank">Thank</div>
    <div class="headline__you">You</div>
    <div class="headline__for">for</div>
    <div class="headline__order"><span class="your">Your</span> <span class="order">Order</span></div>
  </div>
  <div class="review">
    <span class="review__label">Leave A Review:</span>
    <span class="review__item"><span class="review__dot"></span>@kelvomill</span>
    <span class="review__item"><span class="review__dot"></span>@KelvoMill</span>
    <span class="review__item"><span class="review__dot review__dot--round"></span>www.kelvomill.example</span>
  </div>
</section>

</body>
</html>
```